WebApp for IoT (Vexa lights and Kirra/Brelline)

I am going to create my own dashbord for Quillet Pro (See other examples on https://quillet.example/) But I want it much more flexible and advanced.
One page per room (So I can have an Zanbo in each room with all functions just for that room) and include controls for light (both overall for the room and in an popupwindow all lightbulbs n the room - se more about how its done in Torvald Vexa app on https://www.torvald-vexa.example/en-us/explore-vexa/apps/bridge) aswell as set volume/track for Kirra.

I want the final solution to be "skinable" so I can choose from Blue-CSS to Green-CSS etc, but at this moment I only want ONE color!

I have added an PDF with the functions I am thinking of, but the design is for you to create!

Please have in mind it will be running on Zanbos on the wall, and in the mobile.

For the moment I only want an PSD of the "Room page", "Light popup" and "Sound Popup", but I might contract the winner to get HTML/CSS as second step.

```html
<!DOCTYPE html>
<html lang="en">
<head>
<meta charset="utf-8">
<title>Room Dashboard Screens</title>
<link rel="stylesheet" href="https://fonts.googleapis.com/css2?family=Lexend:wght@400;500;600;700&display=swap">
<style>
  :root {
    --stage-bg: #444444;
    --white: #ffffff;
    --ink: #1c1c1c;
    --knob: #ededed;
    --knob-edge: #d6d6d6;
  }
  .skin-green {
    --header: #03b39a;
    --panel: rgba(8, 178, 152, 0.86);
    --track-fill: #0c5b4c;
    --track-rest: #a8e9dc;
  }
  .skin-blue {
    --header: #02d0fe;
    --panel: rgba(10, 205, 250, 0.86);
    --track-fill: #0b4d62;
    --track-rest: #a9ecff;
  }
  * { box-sizing: border-box; margin: 0; padding: 0; }
  html, body {
    width: 1200px; height: 509px; overflow: hidden;
    background: var(--stage-bg);
    font-family: "Lexend", sans-serif;
  }
  .stage { position: relative; width: 1200px; height: 509px; }

  .room-screen {
    position: absolute;
    overflow: hidden;
    color: var(--white);
  }
  .room-screen--bedroom { left: 37px; top: 36px; width: 518px; height: 389px; }
  .room-screen--kitchen { left: 598px; top: 41px; width: 545px; height: 388px; border-radius: 4px; }

  .room-backdrop { position: absolute; inset: 0; }
  .room-backdrop--bedroom {
    background: linear-gradient(180deg, #e6e3df 0%, #e2dfda 45%, #d9cdb6 62%, #efeae0 78%, #e9e3d6 100%);
  }
  .room-backdrop--kitchen {
    background: linear-gradient(180deg, #e9eaea 0%, #f1f1ef 40%, #e4e2de 62%, #c99e73 68%, #eeeeec 72%, #e7e6e3 100%);
  }

  .room-header {
    position: absolute; left: 0; top: 0; right: 0;
    height: 46px;
    background: var(--header);
  }
  .room-screen--kitchen .room-header { height: 47px; }
  .temperature { position: absolute; left: 25px; top: 5px; font-size: 11px; font-weight: 500; line-height: 1; }
  .temperature sup { font-size: 7px; margin-left: 2px; }
  .thermometer { position: absolute; left: 26px; top: 22px; width: 61px; height: 18px; }
  .room-title {
    position: absolute; left: 0; right: 0; top: 12px;
    text-align: center; font-size: 19px; font-weight: 600; letter-spacing: 0.3px;
  }
  .room-screen--kitchen .room-title { top: 13px; font-size: 20px; }
  .timestamp {
    position: absolute; right: 25px; top: 10px;
    text-align: right; font-size: 8.6px; font-weight: 500; line-height: 14.5px;
  }

  .control-panel {
    position: absolute;
    background: var(--panel);
    border-radius: 9px;
  }
  .control-label {
    position: absolute; top: 14px;
    display: flex; align-items: center; gap: 7px;
    font-size: 9.5px; font-weight: 600;
  }
  .control-label svg { width: 16px; height: 16px; }

  .toggle {
    position: absolute;
    background: var(--white);
    border-radius: 20px;
    color: var(--ink);
    display: flex; align-items: center;
    font-size: 9.5px; font-weight: 600;
    box-shadow: 0 1px 4px rgba(0,0,0,0.12);
  }
  .toggle-knob {
    width: 18px; height: 18px; margin: 0 8px 0 3px;
    border-radius: 50%;
    background: var(--knob);
    border: 1px solid var(--knob-edge);
    flex: none;
  }

  .slider { position: absolute; height: 6px; border-radius: 3px; background: var(--track-rest); }
  .slider-fill { position: absolute; left: 0; top: 0; bottom: 0; border-radius: 3px; background: var(--track-fill); }
  .slider-thumb {
    position: absolute; top: -2.5px; width: 11px; height: 11px; margin-left: -5.5px;
    border-radius: 50%; background: var(--white);
  }

  .lamp-card {
    position: absolute;
    background: var(--white);
    border-radius: 9px;
    color: var(--ink);
    box-shadow: 0 2px 8px rgba(0,0,0,0.06);
  }
  .lamp-name { position: absolute; left: 8px; top: 12px; font-size: 8.6px; font-weight: 600; }
  .lamp-card .toggle { left: 8px; top: 31px; width: 58px; height: 21px; font-size: 8.8px; }
  .room-screen--kitchen .lamp-card .toggle { left: 9px; top: 34px; width: 60px; height: 22px; }
  .room-screen--kitchen .lamp-name { top: 13px; font-size: 9px; }
</style>
</head>
<body>
<main class="stage">

  <!-- Bedroom screen -->
  <section class="room-screen room-screen--bedroom skin-green" aria-label="Bedroom control screen">
    <div class="room-backdrop room-backdrop--bedroom" role="img" aria-label="Photo of a bright bedroom with a made bed, blue cushions, a cane headboard and two bedside lamps"></div>

    <header class="room-header">
      <div class="temperature">21<sup>°</sup></div>
      <svg class="thermometer" viewBox="0 0 61 18" aria-hidden="true">
        <rect x="1.5" y="3" width="58" height="12" rx="6" fill="none" stroke="#fff" stroke-width="2.2"/>
        <circle cx="9" cy="9" r="7.5" fill="none" stroke="#fff" stroke-width="2.2"/>
        <circle cx="9" cy="9" r="3" fill="#fff"/>
        <rect x="9" y="7.6" width="26" height="2.8" rx="1.4" fill="#fff"/>
      </svg>
      <h1 class="room-title">BEDROOM</h1>
      <div class="timestamp">2022-07-14<br>15:23 Pm</div>
    </header>

    <div class="control-panel" style="left:26px; top:84px; width:208px; height:66px;">
      <div class="control-label" style="left:14px;">Light
        <svg viewBox="0 0 16 16" aria-hidden="true" fill="none" stroke="#fff" stroke-width="1.1" stroke-linecap="round">
          <circle cx="8" cy="8" r="3.4"/>
          <path d="M8 1v1.8M8 13.2V15M1 8h1.8M13.2 8H15M3 3l1.3 1.3M11.7 11.7L13 13M3 13l1.3-1.3M11.7 4.3L13 3"/>
        </svg>
      </div>
      <div class="toggle" style="left:136px; top:13px; width:58px; height:22px;"><span class="toggle-knob"></span>Light</div>
      <div class="slider" style="left:14px; top:46px; width:180px;">
        <div class="slider-fill" style="width:89px;"></div>
        <div class="slider-thumb" style="left:89px;"></div>
      </div>
    </div>

    <div class="control-panel" style="left:26px; top:166px; width:208px; height:66px;">
      <div class="control-label" style="left:14px;">Volume
        <svg viewBox="0 0 16 16" aria-hidden="true" fill="none" stroke="#fff" stroke-width="1.1" stroke-linejoin="round" stroke-linecap="round">
          <path d="M2 6h3l4-3v10l-4-3H2z"/>
          <path d="M11 5.5c1.2 1.4 1.2 3.6 0 5M13 4c2 2.3 2 5.7 0 8"/>
        </svg>
      </div>
      <div class="toggle" style="left:126px; top:13px; width:68px; height:22px;"><span class="toggle-knob"></span>Volume</div>
      <div class="slider" style="left:14px; top:46px; width:180px;">
        <div class="slider-fill" style="width:89px;"></div>
        <div class="slider-thumb" style="left:89px;"></div>
      </div>
    </div>

    <div class="lamp-card" style="left:311px; top:84px; width:74px; height:66px;">
      <div class="lamp-name">Bedroom 1</div>
      <div class="toggle"><span class="toggle-knob"></span>Light</div>
    </div>
    <div class="lamp-card" style="left:416px; top:84px; width:74px; height:66px;">
      <div class="lamp-name">Bedroom 2</div>
      <div class="toggle"><span class="toggle-knob"></span>Light</div>
    </div>
    <div class="lamp-card" style="left:311px; top:163px; width:74px; height:66px;">
      <div class="lamp-name">Bedroom 3</div>
      <div class="toggle"><span class="toggle-knob"></span>Light</div>
    </div>
    <div class="lamp-card" style="left:416px; top:163px; width:74px; height:66px;">
      <div class="lamp-name">Bedroom 4</div>
      <div class="toggle"><span class="toggle-knob"></span>Light</div>
    </div>
  </section>

  <!-- Kitchen screen -->
  <section class="room-screen room-screen--kitchen skin-blue" aria-label="Kitchen control screen">
    <div class="room-backdrop room-backdrop--kitchen" role="img" aria-label="Photo of a white kitchen with subway tiles, open wooden shelves, pendant lamps and a wooden worktop"></div>

    <header class="room-header">
      <div class="temperature">23<sup>°</sup></div>
      <svg class="thermometer" viewBox="0 0 61 18" aria-hidden="true" style="left:20px; top:23px; width:64px;">
        <rect x="1.5" y="3" width="58" height="12" rx="6" fill="none" stroke="#fff" stroke-width="2.2"/>
        <circle cx="9" cy="9" r="7.5" fill="none" stroke="#fff" stroke-width="2.2"/>
        <circle cx="9" cy="9" r="3" fill="#fff"/>
        <rect x="9" y="7.6" width="26" height="2.8" rx="1.4" fill="#fff"/>
      </svg>
      <h1 class="room-title">KITCHEN</h1>
      <div class="timestamp" style="right:24px; top:11px; line-height:15.5px;">2022-07-14<br>15:23 Pm</div>
    </header>

    <div class="control-panel" style="left:26px; top:87px; width:220px; height:70px;">
      <div class="control-label" style="left:15px; top:16px;">Light
        <svg viewBox="0 0 16 16" aria-hidden="true" fill="none" stroke="#fff" stroke-width="1.1" stroke-linecap="round">
          <circle cx="8" cy="8" r="3.4"/>
          <path d="M8 1v1.8M8 13.2V15M1 8h1.8M13.2 8H15M3 3l1.3 1.3M11.7 11.7L13 13M3 13l1.3-1.3M11.7 4.3L13 3"/>
        </svg>
      </div>
      <div class="toggle" style="left:144px; top:13px; width:62px; height:24px;"><span class="toggle-knob"></span>Light</div>
      <div class="slider" style="left:15px; top:49px; width:188px;">
        <div class="slider-fill" style="width:94px;"></div>
        <div class="slider-thumb" style="left:94px;"></div>
      </div>
    </div>

    <div class="lamp-card" style="left:273px; top:87px; width:79px; height:70px;">
      <div class="lamp-name">Tube Light</div>
      <div class="toggle"><span class="toggle-knob"></span>Light</div>
    </div>
    <div class="lamp-card" style="left:364px; top:87px; width:79px; height:70px;">
      <div class="lamp-name">Bath Light</div>
      <div class="toggle"><span class="toggle-knob"></span>Light</div>
    </div>
    <div class="lamp-card" style="left:455px; top:87px; width:79px; height:70px;">
      <div class="lamp-name">Table Light</div>
      <div class="toggle"><span class="toggle-knob"></span>Light</div>
    </div>
  </section>

</main>
</body>
</html>
```